My Pebble Porch Path Blog Re-Do Launch

I need a blog makeover. Someone started for me and they sold their company. The blog is primarily spiritual/inspirational. I would eventually like to monetize and launch some ebooks and/or other products. I am open to suggestions. I am learning as we go along, so please keep that in mind. The final design should be warm and welcoming. I am open to suggestions. I am looking to build a relationship.

Target Market(s)

women, moms, females with chronic health issues, moms of special needs kids, those who need encouragement

Industry/Entity Type

Religious

Number of Pages Required

4 page

Font styles to use
Sans Serif

Colors
eddcec
fdf9cf
ffffff

Requirements
Must have
• I would like my main page to have a short about section, relevant posts, recent posts, and archive posts. The main page should also have a place to subscribe as well a search feature.
Nice to have
• Buttons (grab my button), blogs I follow, e-cart capabilities

```html
<!DOCTYPE html>
<html lang="en">
<head>
<meta charset="utf-8">
<title>My Pebble Porch Path</title>
<link href="https://fonts.googleapis.com/css2?family=Montserrat:wght@300;400;700&family=Raleway:wght@400;500;600&display=swap" rel="stylesheet">
<style>
:root{
  --lilac:#c9a3cf;
  --lilac-soft:#eddcec;
  --cream:#fdf9cf;
  --white:#ffffff;
  --ink:#3b3b3b;
  --muted:#9a9a9a;
  --nav:#25272b;
  --footer:#2c2f34;
  --green:#2cc27a;
  --orange:#ea5a1f;
  --gold:#d3b82a;
  --fb:#3b5998;
  --chirp:#3ec3f0;
  --red:#d0202e;
  --line:#e2e2e2;
}
*{box-sizing:border-box;margin:0;padding:0}
html,body{width:675px;height:1200px;overflow:hidden;background:var(--white)}
body{position:relative;font-family:"Raleway",sans-serif;color:var(--ink)}
.abs{position:absolute}

/* hero */
.hero{left:0;top:0;width:675px;height:380px;
  background:linear-gradient(180deg,#3f4656 0%,#6e6a6a 25%,#b48a5a 48%,#d8a45e 55%,#4b4a4e 70%,#2a2c33 100%)}
.hero-title{left:0;width:675px;text-align:center;font-family:"Montserrat",sans-serif}
.hero-title.main{top:150px;font-size:50px;font-weight:700;color:var(--cream);letter-spacing:1px}
.hero-title.sub{top:228px;font-size:40px;font-weight:300;color:var(--white);letter-spacing:2px}
.hero-arrow{top:176px}

/* header */
.brand{left:55px;top:0;width:143px;height:54px;background:var(--white);display:flex;align-items:center;gap:8px;padding-left:12px}
.brand-mark{width:14px;height:14px;background:var(--lilac);border-radius:50%}
.brand-name{font-family:"Montserrat",sans-serif;font-weight:700;font-size:11px;color:#444}
.nav{left:198px;top:0;width:371px;height:54px;background:var(--nav);display:flex}
.nav a{flex:auto;display:flex;align-items:center;justify-content:center;color:var(--white);font-size:7.5px;font-family:"Montserrat",sans-serif;text-decoration:none;border-right:1px solid #34363b}
.search{left:569px;top:0;width:50px;height:54px;background:var(--lilac);display:flex;align-items:center;justify-content:center}

/* relevant strip */
.tag-btn{left:55px;top:399px;width:119px;height:23px;background:var(--lilac);color:var(--white);font-size:8px;font-family:"Montserrat",sans-serif;display:flex;align-items:center;justify-content:center;letter-spacing:.4px}
.strip-thumb{top:399px;width:33px;height:23px}
.strip-link{top:406px;font-size:7.2px;font-family:"Montserrat",sans-serif;text-decoration:underline;color:#555}

/* cards */
.card{background:var(--white);box-shadow:0 1px 2px rgba(0,0,0,.18)}
.photo{position:absolute;left:0;top:0;width:100%}
.card-text{position:absolute;left:8px;right:8px;font-size:6.5px;font-family:"Montserrat",sans-serif;color:#555;line-height:1.9}
.card-label{font-size:7.2px;color:#444;font-weight:400}
.when{color:var(--lilac);font-family:"Raleway",sans-serif;font-size:6.8px;display:flex;align-items:center;gap:4px}
.clock{width:6px;height:6px;border:1px solid var(--lilac);border-radius:50%}
.plus{position:absolute;width:22px;height:22px;border-radius:50%;color:var(--white);font-size:17px;line-height:21px;text-align:center;font-family:"Montserrat",sans-serif;font-weight:300;box-shadow:0 1px 3px rgba(0,0,0,.3)}
.plus.big{width:31px;height:31px;font-size:24px;line-height:30px}
.fav{position:absolute;right:8px;top:7px}

/* section band */
.band{left:55px;top:728px;width:564px;height:54px;background:linear-gradient(90deg,#7b8593,#4c5360 60%,#3a3f4a)}
.band-tab{left:55px;top:728px;width:167px;height:54px;background:var(--lilac);clip-path:polygon(0 0,78% 0,100% 100%,0 100%)}
.band-title{left:66px;top:748px;color:var(--white);font-family:"Montserrat",sans-serif;font-size:11px;font-weight:700;letter-spacing:.3px}

/* pagination */
.pager{left:55px;top:1054px;display:flex;gap:5px}
.pager span{height:15px;min-width:15px;padding:0 4px;border:1px solid #ddd;background:#f6f6f6;font-size:6.5px;font-weight:600;display:flex;align-items:center;justify-content:center;color:#444}
.pager .wide{min-width:29px}

/* actions */
.action{top:1098px;height:23px;color:var(--white);font-family:"Montserrat",sans-serif;font-size:8px;display:flex;align-items:center;justify-content:center;gap:6px}
.action.fb{left:55px;width:152px;background:var(--fb)}
.action.chirp{left:262px;width:150px;background:var(--chirp)}
.action.sub{left:466px;width:153px;background:var(--red);font-weight:700}
.dot{width:8px;height:8px;background:var(--white);border-radius:50%}
.pill{width:34px;height:9px;background:#dfe3ee;border-radius:1px}

/* footer */
.footer{left:0;top:1142px;width:675px;height:58px;background:var(--footer)}
.copy{left:55px;top:1167px;font-size:6px;color:#b8b8b8}
.copy b{color:var(--white);font-weight:500}
.social{left:514px;top:1165px;display:flex;gap:2px}
.social i{width:13px;height:13px;display:block}
</style>
</head>
<body>

<section class="abs hero" role="img" aria-label="Sunset over calm water with a kneeling figure before a cross"></section>
<div class="abs hero-title main">MY PEBBLE</div>
<div class="abs hero-title sub">PORCH PATH</div>
<svg class="abs hero-arrow" style="left:16px" width="16" height="30" viewBox="0 0 16 30"><path d="M14 2 3 15l11 13" fill="none" stroke="rgba(255,255,255,.5)" stroke-width="2.5"/></svg>
<svg class="abs hero-arrow" style="left:642px" width="16" height="30" viewBox="0 0 16 30"><path d="M2 2l11 13L2 28" fill="none" stroke="rgba(255,255,255,.5)" stroke-width="2.5"/></svg>

<header>
  <div class="abs brand"><span class="brand-mark"></span><span class="brand-name">MY PEBBLE</span></div>
  <nav class="abs nav">
    <a href="#">HOME</a><a href="#">ABOUT US</a><a href="#">SERVICES</a><a href="#">BLOG</a><a href="#" style="border:0">CONTACT US</a>
  </nav>
  <div class="abs search"><svg width="9" height="9" viewBox="0 0 10 10"><circle cx="4" cy="4" r="3" fill="none" stroke="#fff" stroke-width="1.5"/><path d="M6.3 6.3 9 9" stroke="#fff" stroke-width="1.5"/></svg></div>
</header>

<div class="abs tag-btn">RELEVANT POSTS</div>
<div class="abs strip-thumb" style="left:188px;background:linear-gradient(#5a6a80,#2d3440)" role="img" aria-label="Three crosses at dusk"></div>
<a class="abs strip-link" style="left:229px">ON THE OTHER HAND, DENOUNCE</a>
<div class="abs strip-thumb" style="left:382px;background:radial-gradient(circle,#d9a55a,#2a1c12 70%)" role="img" aria-label="Lit cross in a corridor"></div>
<a class="abs strip-link" style="left:425px">AT VERO EOS ET ACCUSAMUS ET IUSTO</a>

<!-- featured post -->
<article class="abs card" style="left:55px;top:443px;width:245px;height:260px">
  <div class="photo" style="height:184px;background:linear-gradient(180deg,#d98a86,#b99196 45%,#7d8a88 80%,#3f4c48)" role="img" aria-label="Three crosses on a hill under a pink sky"></div>
  <svg class="fav" width="10" height="22" viewBox="0 0 10 22"><path d="M5 8 1 4a2.2 2.2 0 0 1 4-2 2.2 2.2 0 0 1 4 2z" fill="#fff"/><circle cx="5" cy="13" r="1.2" fill="#fff"/><circle cx="5" cy="17" r="1.2" fill="#fff"/><circle cx="5" cy="21" r="1.2" fill="#fff"/></svg>
  <div class="plus big" style="left:203px;top:166px;background:var(--lilac)">+</div>
  <div class="card-text" style="top:205px">AT VERO EOS ET ACCUSAMUS ET IUSTO ODIO DIGNISSIMOS DUCIMUS
    <div class="when" style="margin-top:4px"><span class="clock"></span>4 months ago</div></div>
</article>

<article class="abs card" style="left:312px;top:443px;width:144px;height:119px">
  <div class="photo" style="height:81px;background:linear-gradient(135deg,#2e3f66,#6a5a6a 50%,#c9a07a)" role="img" aria-label="Cross against blurred lights"></div>
  <svg class="fav" width="10" height="22" viewBox="0 0 10 22"><path d="M5 8 1 4a2.2 2.2 0 0 1 4-2 2.2 2.2 0 0 1 4 2z" fill="#fff"/><circle cx="5" cy="13" r="1.2" fill="#fff"/><circle cx="5" cy="17" r="1.2" fill="#fff"/></svg>
  <div class="plus" style="left:116px;top:69px;background:var(--green)">+</div>
  <div class="card-text" style="top:87px">AT VERO EOS ET ACCUSAMUS ET<div class="when"><span class="clock"></span>4 months ago</div></div>
</article>

<article class="abs card" style="left:475px;top:443px;width:144px;height:119px">
  <div class="photo" style="height:81px;background:linear-gradient(135deg,#8aa0b0,#c6b9a8 50%,#8a3a3a)" role="img" aria-label="Cross draped with red cloth"></div>
  <svg class="fav" width="10" height="22" viewBox="0 0 10 22"><path d="M5 8 1 4a2.2 2.2 0 0 1 4-2 2.2 2.2 0 0 1 4 2z" fill="#fff"/><circle cx="5" cy="13" r="1.2" fill="#fff"/><circle cx="5" cy="17" r="1.2" fill="#fff"/></svg>
  <div class="plus" style="left:116px;top:69px;background:var(--orange)">+</div>
  <div class="card-text" style="top:87px">AT VERO EOS ET ACCUSAMUS ET<div class="when"><span class="clock"></span>4 months ago</div></div>
</article>

<article class="abs card" style="left:312px;top:585px;width:144px;height:118px">
  <div class="photo" style="height:80px;background:linear-gradient(135deg,#d9852a,#6a3a18 55%,#1e1410)" role="img" aria-label="Silhouetted cross against golden light"></div>
  <svg class="fav" width="10" height="22" viewBox="0 0 10 22"><path d="M5 8 1 4a2.2 2.2 0 0 1 4-2 2.2 2.2 0 0 1 4 2z" fill="#fff"/><circle cx="5" cy="13" r="1.2" fill="#fff"/><circle cx="5" cy="17" r="1.2" fill="#fff"/></svg>
  <div class="plus" style="left:116px;top:68px;background:var(--green)">+</div>
  <div class="card-text" style="top:86px">AT VERO EOS ET ACCUSAMUS ET<div class="when"><span class="clock"></span>4 months ago</div></div>
</article>

<article class="abs card" style="left:475px;top:585px;width:144px;height:118px">
  <div class="photo" style="height:80px;background:linear-gradient(135deg,#4d8a96,#6aa3a8 50%,#3a6a70)" role="img" aria-label="Wooden cross on teal painted wall"></div>
  <svg class="fav" width="10" height="22" viewBox="0 0 10 22"><path d="M5 8 1 4a2.2 2.2 0 0 1 4-2 2.2 2.2 0 0 1 4 2z" fill="#fff"/><circle cx="5" cy="13" r="1.2" fill="#fff"/><circle cx="5" cy="17" r="1.2" fill="#fff"/></svg>
  <div class="plus" style="left:116px;top:68px;background:var(--orange)">+</div>
  <div class="card-text" style="top:86px">AT VERO EOS ET ACCUSAMUS ET<div class="when"><span class="clock"></span>4 months ago</div></div>
</article>

<div class="abs band" role="img" aria-label="Cross silhouette against an evening sky"></div>
<div class="abs band-tab"></div>
<h2 class="abs band-title">E-CART CAPABILITIES</h2>

<article class="abs card" style="left:55px;top:809px;width:177px;height:223px">
  <div class="photo" style="height:141px;background:linear-gradient(135deg,#9aa58a,#6e6a4e 50%,#4a4032)" role="img" aria-label="Crown of thorns and nails"></div>
  <svg class="fav" width="10" height="22" viewBox="0 0 10 22"><path d="M5 8 1 4a2.2 2.2 0 0 1 4-2 2.2 2.2 0 0 1 4 2z" fill="#fff"/><circle cx="5" cy="13" r="1.2" fill="#fff"/><circle cx="5" cy="17" r="1.2" fill="#fff"/><circle cx="5" cy="21" r="1.2" fill="#fff"/></svg>
  <div class="plus" style="left:144px;top:128px;background:var(--orange)">+</div>
  <div class="card-text" style="top:152px"><div class="card-label">RECENT POSTS</div>AT VERO EOS ET ACCUSAMUS ET IUSTO ODIO DIGNISSIMOS<div class="when"><span class="clock"></span>4 months ago</div></div>
</article>

<article class="abs card" style="left:250px;top:809px;width:176px;height:223px">
  <div class="photo" style="height:141px;background:radial-gradient(circle at 70% 35%,#bcd4e6,#2a4a66 35%,#0a0f18 75%)" role="img" aria-label="Cross with light rays in darkness"></div>
  <svg class="fav" width="10" height="22" viewBox="0 0 10 22"><path d="M5 8 1 4a2.2 2.2 0 0 1 4-2 2.2 2.2 0 0 1 4 2z" fill="#fff"/></svg>
  <div class="plus" style="left:143px;top:128px;background:var(--green)">+</div>
  <div class="card-text" style="top:152px"><div class="card-label">ARCHIVE POSTS</div>AT VERO EOS ET ACCUSAMUS ET IUSTO ODIO DIGNISSIMOS<div class="when"><span class="clock"></span>4 months ago</div></div>
</article>

<article class="abs card" style="left:443px;top:809px;width:176px;height:223px">
  <div class="photo" style="height:141px;background:radial-gradient(circle at 50% 50%,#e6c089,#6a4218 30%,#140c06 75%)" role="img" aria-label="Candlelit corridor leading to a cross"></div>
  <svg class="fav" width="10" height="22" viewBox="0 0 10 22"><path d="M5 8 1 4a2.2 2.2 0 0 1 4-2 2.2 2.2 0 0 1 4 2z" fill="#fff"/><circle cx="5" cy="13" r="1.2" fill="#fff"/><circle cx="5" cy="17" r="1.2" fill="#fff"/><circle cx="5" cy="21" r="1.2" fill="#fff"/></svg>
  <div class="plus" style="left:143px;top:128px;background:var(--gold)">+</div>
  <div class="card-text" style="top:152px"><div class="card-label">RELEVANT POSTS</div>AT VERO EOS ET ACCUSAMUS ET IUSTO ODIO DIGNISSIMOS<div class="when"><span class="clock"></span>4 months ago</div></div>
</article>

<nav class="abs pager">
  <span class="wide">Prev</span><span>1</span><span>2</span><span>3</span><span>4</span><span>5</span><span>6</span><span>…</span><span>22</span><span class="wide">Next</span>
</nav>

<a class="abs action fb"><span class="dot"></span>LIKE US ON FRIENDPAGE<span class="pill"></span></a>
<a class="abs action chirp"><span class="dot"></span>JOIN US</a>
<a class="abs action sub">SUBSCRIBE NOW</a>

<footer class="abs footer"></footer>
<p class="abs copy">Copyright 2015 – <b>My Pebble Porch Path.</b> // All Right Reserved</p>
<div class="abs social">
  <i style="background:#3b5998"></i><i style="background:#3ec3f0"></i><i style="background:#f7931e"></i><i style="background:#dd4b39"></i><i style="background:#cc181e"></i><i style="background:#b8b8b8"></i><i style="background:#ff6a1f"></i>
</div>

</body>
</html>
```